Wordpress Design (uncoded) Auction & Real Estate 3 in 1

This will be an uncoded Wordpress theme design only. Winning designer will provide PSD source files.

We need a wordpress themedesign for an established auction and real estate company based in Pennsylvania. The client wants one overall theme for their primary company website with 2 child themes, one for auction division and one for real estate division. Each child theme will have it's own color scheme and some variation in layout.

The primary company logo is Blue with white/black/silver elements. (see attached zip file)

The auction division logo is Gold with black/white elements (see attached zip file)

The real estate division logo is Green with white/black/silver elements. (see attached zip file)

Also attached are 2 PDF files showing a sample layout that the client came up with that they really like; however, this should only be used as a starting point. We want to see what creative, clean layouts you can come up with.

Industry/Entity Type

Real Estate

Requirements
Must have
• - We will require winning designer to provide a layered PSD (Adobe photoshop) concept files, along with any non-standard font files used.

A slideshow element on the home page using the placeholder image provided.

Primary Site navigation for merrowtonhalvecompanies.example:

Home
Services
-Auctions/Appraisals
-Real Estate Auctions
-Real Estate Listings
About Us
-History
-Auction Center
Contact Us

Secondary site - halvegavelhouse.example navigation:
Home
Auctions
Buy/Sell
Collections
Services
Contact Us

Secondary site - merrowtonhalve.example
Home
Properties
Real Estate Auctions
Buying
Selling
Area Info
About Us
Contact Us
Nice to have
• Sidebar widgets: Email sign-up form - Featured Auctions - Featured Assets for Sale

```html
<!DOCTYPE html>
<html lang="en">
<head>
<meta charset="utf-8">
<title>Merrowton Halve Real Estate</title>
<link href="https://fonts.googleapis.com/css2?family=Arimo:wght@400;700&family=Delius&family=Delius+Swash+Caps&display=swap" rel="stylesheet">
<style>
:root{
  --green:#2e6b47;
  --green-dark:#1f4a31;
  --green-deep:#244f36;
  --ink:#1a1a1a;
  --grey:#555;
  --panel:#ebe8e6;
  --header-grey:#5a5a5a;
  --page:#f1f1f1;
  --bar:#231f20;
}
*{box-sizing:border-box;margin:0;padding:0}
html,body{width:1027px;height:1200px;overflow:hidden}
body{position:relative;background:var(--page);font-family:Arimo,Arial,sans-serif;color:var(--ink)}
.abs{position:absolute}
.header{left:0;top:0;width:1027px;height:97px;background:#f6f6f6}
.brand{left:128px;top:26px;display:flex;align-items:center;gap:8px}
.brand-dot{width:34px;height:34px;border-radius:50%;background:var(--green)}
.brand-name{font-family:Arimo,sans-serif;font-weight:700;font-size:19px;color:var(--green);line-height:1.05}
.tagline{right:128px;top:34px;font-family:Delius,sans-serif;font-style:italic;font-size:18px;color:var(--green)}
.nav{left:0;top:97px;width:1027px;height:43px;background:linear-gradient(#3d7a55,var(--green-dark))}
.nav ul{position:absolute;left:128px;width:770px;height:43px;display:flex;justify-content:space-between;list-style:none}
.nav li{color:#fff;font-size:12px;line-height:43px;padding:0 13px}
.nav li.active{background:#2a2526}
.slider{left:128px;top:140px;width:770px;height:226px;background:#fff;box-shadow:0 1px 3px rgba(0,0,0,.2)}
.slide{left:8px;top:8px;width:754px;height:210px;background:linear-gradient(90deg,#1e3f27 0%,#5a6a52 35%,#7aa3b5 60%,#6d7d45 85%,#2d4a24 100%)}
.dots{left:338px;top:190px;display:flex;gap:5px}
.dots span{width:15px;height:15px;border-radius:50%;background:#6b6b6b;border:2px solid #ddd}
.dots span.on{background:var(--green)}
.search{left:128px;top:366px;width:770px;height:231px;background:radial-gradient(ellipse at 50% 40%,#37795a,var(--green-deep))}
.search h2{position:absolute;left:24px;top:20px;font-family:Delius,sans-serif;font-weight:400;font-size:23px;color:#fff}
.field{position:absolute;color:#fff;font-size:12px;display:flex;align-items:center}
.select{position:absolute;height:20px;background:linear-gradient(#fff,#dcdcdc);border:1px solid #bbb}
.select::after{content:"";position:absolute;right:5px;top:4px;width:11px;height:10px;background:#c4d2ee;border:1px solid #8ca0c8}
.btn{position:absolute;background:linear-gradient(#fff,#d9d9d9);border:1px solid #bbb;border-radius:6px;color:#444;font-size:14px;display:flex;align-items:center;justify-content:center;box-shadow:0 1px 2px rgba(0,0,0,.3)}
.welcome{left:128px;top:597px;width:770px;height:328px;background:#fff}
.welcome h1{position:absolute;left:24px;top:30px;font-family:"Delius Swash Caps",Delius,cursive;font-style:italic;font-weight:400;font-size:22px;color:#111}
.welcome p{position:absolute;left:25px;top:68px;width:440px;font-size:11.5px;line-height:19.3px}
.auctions{left:614px;top:616px;width:284px;height:286px;background:var(--panel)}
.auctions h3{height:40px;background:var(--header-grey);color:#fff;font-weight:400;font-size:14px;line-height:40px;padding-left:14px}
.item{position:absolute;left:15px;width:260px;font-size:9.5px;color:#555;line-height:14.5px}
.item h4{font-size:11.5px;color:#444;margin-bottom:6px}
.item .date{margin-bottom:6px}
.item a{color:#333;font-weight:700;text-decoration:underline}
.partners{left:128px;top:925px;width:770px;height:103px;background:#fff;display:flex}
.partner{flex:1;display:flex;align-items:center;justify-content:center;gap:7px;border-right:1px solid #e3e3e3}
.partner:last-child{border-right:0}
.partner-mark{width:22px;height:22px;border-radius:50%}
.partner-name{font-weight:700;font-size:14px}
.darkbar{left:0;top:1028px;width:1027px;height:9px;background:var(--bar)}
.footer{left:0;top:1037px;width:1027px;height:163px;background:#fff}
.footer-brand{left:132px;top:43px;display:flex;align-items:center;gap:8px}
.footer-brand .brand-dot{background:#c9c9c9}
.footer-brand .brand-name{color:#bdbdbd}
.footer-info{right:128px;top:47px;text-align:left;font-size:8.5px;font-weight:700;color:#444;line-height:17.5px}
.footer-nav{left:128px;top:108px;width:770px;display:flex;justify-content:space-between;list-style:none;font-size:11.5px}
.footer-nav li{padding:0 4px}
.footer-rule{left:0;top:128px;width:1027px;height:1px;background:#ddd}
.copy{left:0;top:144px;width:1027px;text-align:center;font-size:8.5px;color:#444}
</style>
</head>
<body>
<div class="abs header"></div>
<div class="abs brand">
  <span class="brand-dot"></span>
  <span class="brand-name">MERROWTON HALVE<br>REAL ESTATE</span>
</div>
<div class="abs tagline">Helping people through the maze of property in transition.</div>

<nav class="abs nav">
  <ul>
    <li class="active">HOME</li><li>PROPERTIES</li><li>REAL ESTATE AUCTIONS</li><li>BUYING</li><li>SELLING</li><li>AREA INFO</li><li>ABOUT US</li><li>CONTACT US</li>
  </ul>
</nav>

<section class="abs slider">
  <div class="abs slide" role="img" aria-label="Slideshow photo: wooden gazebo on the shore of a wooded lake in autumn"></div>
  <div class="abs dots" style="left:458px;top:273px"></div>
</section>
<div class="abs dots" style="left:466px;top:336px"><span></span><span></span><span class="on"></span><span></span><span></span></div>

<section class="abs search">
  <h2>Quick Search</h2>
  <div class="field" style="left:30px;top:71px">Select County:</div>
  <div class="select" style="left:110px;top:62px;width:147px"></div>
  <div class="field" style="left:30px;top:110px">Select Town:</div>
  <div class="select" style="left:110px;top:101px;width:147px"></div>
  <div class="field" style="left:292px;top:71px">Min Price:</div>
  <div class="select" style="left:349px;top:62px;width:147px"></div>
  <div class="field" style="left:292px;top:110px">Max Price:</div>
  <div class="select" style="left:349px;top:101px;width:147px"></div>
  <div class="field" style="left:517px;top:71px">Bedrooms:</div>
  <div class="select" style="left:578px;top:62px;width:54px"></div>
  <div class="field" style="left:517px;top:110px">Baths:</div>
  <div class="select" style="left:578px;top:101px;width:54px"></div>
  <div class="btn" style="left:442px;top:151px;width:192px;height:42px">Submit Search</div>
</section>

<section class="abs welcome">
  <h1>Welcome to Merrowton Halve Real Estate</h1>
  <p>Your solution for buying or selling residential, commercial and investment real estate. Our experience in full service brokerage and auction sales make us uniquely qualified to deliver optimum results. Merrowton Halve Real Estate is part of the Merrowton Halve Companies, providing auction, appraisal, real estate, moving and storage services since 1959. Our expertise allows you to buy it, sell it, move it, and store it.</p>
</section>

<aside class="abs auctions">
  <h3>Upcoming Real Estate Auctions</h3>
  <div class="item" style="top:50px">
    <h4>Real Estate Auction 1</h4>
    <div class="date">Apr 17, 2013</div>
    <div>Lorem ipsum dolor sit amet consecutor. Lorem ipsum dolor sit amet consecutor. <a>Read More...</a></div>
  </div>
  <div class="item" style="top:141px">
    <h4>Real Estate Auction 1</h4>
    <div class="date">Apr 17, 2013</div>
    <div>Lorem ipsum dolor sit amet consecutor. Lorem ipsum dolor sit amet consecutor. <a>Read More...</a></div>
  </div>
  <div class="btn" style="left:88px;top:230px;width:137px;height:42px">View All</div>
</aside>

<section class="abs partners">
  <div class="partner"><span class="partner-mark" style="background:#8a7a55"></span><span class="partner-name" style="color:#6e5e3c">Halve Gavel House</span></div>
  <div class="partner"><span class="partner-mark" style="background:#1f4f93"></span><span class="partner-name" style="color:#1f4f93">Merrowton Halve Companies</span></div>
  <div class="partner"><span class="partner-name" style="color:#1d3f6e">Trevant Halve</span></div>
</section>

<div class="abs darkbar"></div>
<footer class="abs footer">
  <div class="abs footer-brand">
    <span class="brand-dot"></span>
    <span class="brand-name">MERROWTON HALVE<br>REAL ESTATE</span>
  </div>
  <div class="abs footer-info">Merrowton Halve Real Estate • 214 Orchard Hill Road • Linvale, Pa 19000 • toll free: 800.555.0142 • phone: 215.555.0187<br>License # RB041973K</div>
  <ul class="abs footer-nav">
    <li>HOME</li><li>PROPERTIES</li><li>REAL ESTATE AUCTIONS</li><li>BUYING</li><li>SELLING</li><li>AREA INFO</li><li>ABOUT US</li><li>CONTACT US</li>
  </ul>
  <div class="abs footer-rule"></div>
  <div class="abs copy">©2013 The Merrowton Halve Real Estate</div>
</footer>
</body>
</html>
```